New Business card design to reflect rebrand

I would like a business card design with a good base colour for our new logo and also a placeholder for a profile pic of the card holder. the design needs to be editable to the point that we can easily change the picture of the person and use that design for printmerlo etc. we are looking at a metalic finish business card so will need a good base colour to bring out the finish.

Target Market(s)

prospective customers

Industry/Entity Type

Business

Contact Information for Business Card

I would like one editable design that we can change the name of the card holder and profile picture. The design need to be in a format that be send to printmerlo etc.

Our address is Fenwick Lodge, Copse Lane, Bramley Heath, GU14 3TP Tel no. 01483 556172

Requirements
Must have
• place holder for a profile pic for the card holder. in AI or preferably PSD format

```html
<!DOCTYPE html>
<html lang="en">
<head>
<meta charset="utf-8">
<title>Brellcor Workplace Services – Business Card</title>
<link rel="stylesheet" href="https://fonts.googleapis.com/css2?family=Source+Sans+3:wght@400;600&display=swap">
<style>
  :root {
    --stage: #e9e7e4;
    --card-black: #050505;
    --card-glow: #1e1e1e;
    --accent-orange: #f26a10;
    --accent-slate: #4f6580;
    --text-white: #ffffff;
    --photo-light: #6d6a68;
    --photo-dark: #1a1a1c;
  }
  * { box-sizing: border-box; margin: 0; padding: 0; }
  html, body { width: 1200px; height: 844px; overflow: hidden; }
  body {
    background: var(--stage);
    font-family: "Source Sans 3", "Segoe UI", sans-serif;
    position: relative;
  }
  .card {
    position: absolute;
    top: 273px;
    width: 505px;
    height: 297px;
    background: var(--card-black);
    overflow: hidden;
    box-shadow: 0 6px 18px rgba(0,0,0,0.25);
  }
  /* Front */
  .card--front { left: 70px; }
  .front__band-top {
    position: absolute; left: 0; top: 0; width: 100%; height: 13px;
    background: var(--accent-orange);
  }
  .front__band-bottom {
    position: absolute; left: 0; bottom: 0; width: 100%; height: 13px;
    background: var(--accent-slate);
  }
  .front__photo {
    position: absolute; left: 0; top: 13px; bottom: 13px; width: 235px;
    background:
      radial-gradient(ellipse 60% 55% at 45% 42%, var(--photo-light) 0%, rgba(109,106,104,0) 70%),
      linear-gradient(180deg, #2a2a2c 0%, var(--photo-dark) 100%);
  }
  .front__details {
    position: absolute; left: 235px; right: 0; top: 60px;
    text-align: center; color: var(--text-white);
  }
  .holder-name {
    font-size: 25px; font-weight: 600; letter-spacing: 0.2px; margin-bottom: 22px;
  }
  .holder-name__first { color: var(--accent-orange); }
  .holder-name__last { color: var(--accent-slate); }
  .contact-line { font-size: 13.5px; line-height: 19px; }
  .contact-address { margin-top: 26px; }

  /* Back */
  .card--back {
    left: 625px;
    background: radial-gradient(ellipse 60% 60% at 55% 40%, var(--card-glow) 0%, var(--card-black) 75%);
  }
  .back__tab-orange {
    position: absolute; right: 0; top: 24px; width: 30px; height: 30px;
    background: var(--accent-orange);
  }
  .back__tab-slate {
    position: absolute; left: 0; top: 148px; width: 22px; height: 44px;
    background: var(--accent-slate);
  }
  .brand {
    position: absolute; left: 0; right: 0; top: 104px;
    text-align: center; color: var(--accent-slate);
    font-weight: 600; text-transform: uppercase;
  }
  .brand__name { font-size: 46px; letter-spacing: 3px; line-height: 1; }
  .brand__sub { font-size: 17px; letter-spacing: 3.5px; margin-top: 6px; }
</style>
</head>
<body>
  <section class="card card--front" aria-label="Business card front">
    <div class="front__band-top"></div>
    <div class="front__photo" role="img" aria-label="Profile photo of the card holder"></div>
    <div class="front__details">
      <p class="holder-name"><span class="holder-name__first">Daniel</span> <span class="holder-name__last">Hurst</span></p>
      <p class="contact-line">01483 556172</p>
      <p class="contact-line">info@brellcor.com</p>
      <div class="contact-address">
        <p class="contact-line">Fenwick Lodge, Copse Lane,</p>
        <p class="contact-line">Bramley Heath, GU14 3TP</p>
      </div>
    </div>
    <div class="front__band-bottom"></div>
  </section>

  <section class="card card--back" aria-label="Business card back">
    <div class="back__tab-orange"></div>
    <div class="back__tab-slate"></div>
    <div class="brand">
      <p class="brand__name">Brellcor</p>
      <p class="brand__sub">Workplace Services</p>
    </div>
  </section>
</body>
</html>
```